Business Card Design

I'm a commercial general contractor remodel offices, hotels, health clubs and stores mostly San Francisco and the peninsula
the file I down loaded is kind of what I want I like the I beam with my company name in it, that would be fine with me but if you have better Idea will look at it you never know, I'm decided to give in and change my company name to how every one knows me, I have been in business since 1991, I like the I beam logo I included one of my old card from my old company for reference for you.

BROCK CONSTRUCTION (is my company name)
Warren Pelkey contractor, LIc 514387
3148 Larkspur Row, San Bruno, California 94071
mobile, (415) 736-4052
phone (650) 514-2087
Fax, (650) 514-2088
email, brock@brockconstruction.example

```html
<!DOCTYPE html>
<html lang="en">
<head>
<meta charset="utf-8">
<title>Brock Construction — Business Card</title>
<link rel="stylesheet" href="https://fonts.googleapis.com/css2?family=Source+Sans+3:wght@400;600&display=swap">
<style>
  :root {
    --backdrop: #1d1d20;
    --card: #2f3035;
    --ink: #f4f5f7;
    --accent: #1f8fd8;
    --radius: 16px;
  }
  * { margin: 0; padding: 0; box-sizing: border-box; }
  html, body {
    width: 1200px;
    height: 900px;
    overflow: hidden;
    background: var(--backdrop);
    font-family: "Source Sans 3", sans-serif;
    color: var(--ink);
  }
  .canvas { position: relative; width: 1200px; height: 900px; }
  .card {
    position: absolute;
    left: 331px;
    width: 541px;
    height: 315px;
    background: var(--card);
    border-radius: var(--radius);
  }
  .card--front { top: 121px; }
  .card--back { top: 489px; }

  .wordmark {
    position: absolute;
    color: var(--accent);
    font-weight: 600;
    letter-spacing: 0.02em;
    white-space: nowrap;
    text-transform: uppercase;
  }
  .card--front .wordmark {
    left: 57px;
    top: 152px;
    font-size: 17px;
  }
  .card--back .wordmark {
    left: 0;
    right: 0;
    top: 132px;
    text-align: center;
    font-size: 38px;
  }

  .contact {
    position: absolute;
    left: 282px;
    top: 45px;
    font-size: 15.5px;
    line-height: 20px;
  }
  .contact__name {
    font-size: 24px;
    line-height: 28px;
    font-weight: 400;
    text-transform: uppercase;
    letter-spacing: 0.01em;
  }
  .contact__role { color: var(--accent); margin-top: 1px; }
  .contact__licence { margin-top: 2px; }
  .contact__address { margin-top: 9px; }
  .contact__lines { list-style: none; margin-top: 10px; }
  .contact__lines li { height: 25.5px; line-height: 20px; }
  .contact__label { color: var(--accent); }
</style>
</head>
<body>
<main class="canvas">
  <section class="card card--front" aria-label="Business card front">
    <div class="wordmark">Brock Construction</div>
    <div class="contact">
      <h1 class="contact__name">Warren Pelkey</h1>
      <p class="contact__role">Contractor,</p>
      <p class="contact__licence">Llc 514387</p>
      <p class="contact__address">3148 Larkspur Row,San Bruno,<br>California 94071</p>
      <ul class="contact__lines">
        <li><span class="contact__label">M:</span> (415) 736-4052</li>
        <li><span class="contact__label">T:</span>(650) 514-2087</li>
        <li><span class="contact__label">F:</span>(650) 514-2088</li>
        <li><span class="contact__label">E:</span>brock@brockconstruction.example</li>
      </ul>
    </div>
  </section>

  <section class="card card--back" aria-label="Business card back">
    <div class="wordmark">Brock Construction</div>
  </section>
</main>
</body>
</html>
```